Business Cards for IT Consulting Company (Managed Service Provider)

I am looking to have some business cards printed and would like some designs. We are an IT Consulting company based in Vancouver BC. I would like a nice clean and modern look to the cards. I have uploaded all the versions of my logo so parts can be used as needed. Here is a snippit from our website homepage:

Quillbrook Networks Ltd. is an IT Solutions Partner located in Vancouver BC, Canada. We offer IT solutions and support to customers in the greater Vancouver Area. With expertise in Microsoft platforms, as well as Linux and Mac OSX and over 12 years experience in the IT industry, Quillbrook Networks is dedicated to offering our clients top quality service and products. We take pride in the solutions we offer our customers. The greatest compliment a client can give us is to recommend our services.

Quillbrook Networks Ltd. offers a wide range of IT services from onsite service to remote support and managed service solutions. This allows clients to choose the support path that best suits their company’s needs. Supporting many different sized companies from small to enterprise level over the past 12 years Quillbrook Networks has the experience and expertise needed to ensure things run smoothly. Allowing our clients to focus on doing business.

Revolutionizing the way IT services are delivered.

Quillbrook Networks is dedicated to providing our clients with IT solutions that work and grow with them for years to come. This philosophy helps save money in the long run instead of replacing equipment constantly. Far too often IT solutions are not well thought out and while possibly solving the problem at hand, require replacement due to growth or quality within a very short time frame. Quillbrook Networks takes pride in providing solutions that will last and be able to accommodate growth without the need for replacement.

Industry/Entity Type

Information Technology

Contact Information for Business Card

Quillbrook Networks Ltd.
(Employee Name)
Eml: (Employees Email Address)
Web: quillbrook.me
Ph: 604-555-0148

Font styles to use
Serif
Sans Serif

Requirements
Must have
• The Company logo and company colors.
Nice to have
• - Our tag line: "Building IT That Lasts" or "Revolutionizing the way IT services are delivered."
• - Also I really like the idea of nature and technology together blending which is sort of where my logo came from so integrating that somehow onto the business cards would be great.

```html
<!DOCTYPE html>
<html lang="en">
<head>
<meta charset="utf-8">
<title>Quillbrook Networks – Business Cards</title>
<link rel="stylesheet" href="https://fonts.googleapis.com/css2?family=Lato:wght@300;400;700;900&display=swap">
<style>
  :root {
    --backdrop: #2b2b2d;
    --card-light: #ffffff;
    --card-shade: #e4e5e7;
    --band-grey: #4a4b4f;
    --brand-blue: #1b9ad6;
    --text-grey: #8a8b8e;
    --text-light: #e6e7e9;
  }
  * { box-sizing: border-box; margin: 0; padding: 0; }
  html, body {
    width: 1200px; height: 997px; overflow: hidden;
    background: var(--backdrop);
    font-family: "Lato", Arial, sans-serif;
  }
  .canvas { position: relative; width: 1200px; height: 997px; }
  .card {
    position: absolute; width: 580px; height: 330px;
    border-radius: 22px; overflow: hidden;
    background: linear-gradient(160deg, var(--card-light) 0%, var(--card-light) 45%, var(--card-shade) 100%);
  }
  .card-back { left: 90px; top: 120px; }
  .card-front { left: 530px; top: 540px; }
  .card-art { position: absolute; inset: 0; }
  .band { fill: var(--band-grey); }
  .stripe { fill: var(--brand-blue); }

  .wordmark {
    display: flex; align-items: center; gap: 12px;
    color: var(--brand-blue); font-weight: 900; white-space: nowrap;
  }
  .wordmark-square { background: var(--brand-blue); flex: none; }

  .card-back .wordmark { position: absolute; right: 34px; top: 34px; font-size: 22px; }
  .card-back .wordmark-square { width: 22px; height: 22px; }
  .holder { position: absolute; left: 40px; top: 128px; }
  .holder-name { color: var(--brand-blue); font-weight: 700; font-size: 19px; }
  .holder-role { color: var(--text-grey); font-weight: 400; font-size: 13px; margin-top: 2px; }
  .contacts { position: absolute; left: 40px; top: 236px; list-style: none; }
  .contacts li {
    display: flex; align-items: center; gap: 10px;
    color: var(--text-light); font-weight: 300; font-size: 14px; height: 21px;
  }
  .contacts svg { width: 13px; height: 13px; fill: var(--text-light); flex: none; }

  .card-front .brand-block { position: absolute; left: 95px; top: 92px; }
  .card-front .wordmark { font-size: 34px; }
  .card-front .wordmark-square { width: 30px; height: 30px; }
  .tagline {
    margin-top: 6px; margin-left: 42px;
    color: var(--brand-blue); font-weight: 400; font-size: 16px; letter-spacing: 3px;
  }
  .web {
    position: absolute; right: 36px; bottom: 28px;
    color: var(--text-light); font-weight: 400; font-size: 16px; letter-spacing: 4px;
  }
</style>
</head>
<body>
<main class="canvas">

  <section class="card card-back">
    <svg class="card-art" viewBox="0 0 580 330" preserveAspectRatio="none" aria-hidden="true">
      <path class="band" d="M0 330 L0 238 C160 190 390 152 580 150 L580 330 Z"/>
      <path class="stripe" d="M0 222 C160 172 390 134 580 128 L580 137 C390 146 160 186 0 234 Z"/>
    </svg>
    <div class="wordmark"><span class="wordmark-square"></span>Quillbrook Networks Ltd.</div>
    <div class="holder">
      <p class="holder-name">Dana Orlow</p>
      <p class="holder-role">Creative Head</p>
    </div>
    <ul class="contacts">
      <li><svg viewBox="0 0 16 16"><path d="M3 1l3 3-2 2c1 2 3 4 5 5l2-2 3 3-2 3C6 15 1 10 1 3z"/></svg>604-555-0148</li>
      <li><svg viewBox="0 0 16 16"><path d="M4 1h8v14H4z M5.5 2.5v9h5v-9z"/></svg>604-555-0193</li>
      <li><svg viewBox="0 0 16 16"><path d="M1 3h14v10H1z M2 4l6 5 6-5z" fill-rule="evenodd"/></svg>dorlow@quillbrook.me</li>
      <li><svg viewBox="0 0 16 16"><path d="M8 1a5 5 0 0 1 5 5c0 4-5 9-5 9S3 10 3 6a5 5 0 0 1 5-5zm0 3a2 2 0 1 0 0 4 2 2 0 0 0 0-4z" fill-rule="evenodd"/></svg>Harbourview Road 27, Vancouver BC</li>
    </ul>
  </section>

  <section class="card card-front">
    <svg class="card-art" viewBox="0 0 580 330" preserveAspectRatio="none" aria-hidden="true">
      <path class="band" d="M230 330 C330 270 450 232 580 218 L580 330 Z"/>
      <path class="stripe" d="M300 258 C390 214 480 190 580 178 L580 190 C480 200 390 226 300 258 Z"/>
    </svg>
    <div class="brand-block">
      <div class="wordmark"><span class="wordmark-square"></span>Quillbrook Networks Ltd.</div>
      <p class="tagline">Building IT That Lasts</p>
    </div>
    <p class="web">www.quillbrook.me</p>
  </section>

</main>
</body>
</html>
```